Specialised investor in e-mobility and energy wants business card design

We need a business card design that fits our existing corporate design. <The look and feel must be 'sharp'/'clean', dynamic, communicate momentum, professionalism etc (as one would imagine from a firm in the financial sector). We like the idea of a reverse-side of the card that includes the logo, and the name and contact details on the other. We expect the deliverable to be whatever format might be required to be able to get cards printed directly by a service such as kelmo press. Our website is www.zub.capital

```html
<!DOCTYPE html>
<html lang="en">
<head>
<meta charset="utf-8">
<title>Zub Capital – Business Card</title>
<link rel="stylesheet" href="https://fonts.googleapis.com/css2?family=Bebas+Neue&family=Arimo:wght@400&display=swap">
<style>
  :root {
    --stage: #121412;
    --card: #2b4a20;
    --card-deep: #1f3917;
    --accent: #7ab33e;
    --edge: #6aa233;
    --ink: #ffffff;
    --ink-soft: #e6ecdf;
  }
  * { box-sizing: border-box; margin: 0; padding: 0; }
  html, body { width: 1200px; height: 963px; overflow: hidden; }
  body {
    background: var(--stage);
    font-family: "Arimo", Arial, sans-serif;
    position: relative;
  }
  .card {
    position: absolute;
    left: 230px;
    width: 740px;
    height: 423px;
    border-radius: 26px;
    background: linear-gradient(160deg, var(--card) 0%, var(--card-deep) 100%);
    border-bottom: 4px solid var(--edge);
    overflow: hidden;
  }
  .card--front { top: 33px; }
  .card--back { top: 506px; }

  .name {
    position: absolute;
    left: 84px;
    top: 118px;
    font-family: "Bebas Neue", "Arial Narrow", sans-serif;
    font-size: 66px;
    line-height: 1;
    letter-spacing: 1px;
    color: var(--ink);
  }
  .name__last { color: var(--accent); }

  .divider {
    position: absolute;
    left: 432px;
    top: 112px;
    width: 1px;
    height: 120px;
    background: var(--ink-soft);
  }
  .contacts {
    position: absolute;
    left: 456px;
    top: 128px;
    list-style: none;
    font-size: 19px;
    color: var(--ink);
  }
  .contacts li {
    display: flex;
    align-items: center;
    gap: 12px;
    height: 32px;
  }
  .contacts svg { width: 18px; height: 18px; flex: none; }

  .location {
    position: absolute;
    left: 84px;
    bottom: 72px;
    font-size: 19px;
    color: var(--ink-soft);
  }
  .brand {
    position: absolute;
    font-family: "Arimo", Arial, sans-serif;
    font-weight: 400;
    color: var(--ink);
    white-space: nowrap;
  }
  .card--front .brand { right: 70px; bottom: 52px; font-size: 30px; }

  .pattern {
    position: absolute;
    inset: 0;
    background: radial-gradient(circle at 40% 40%, #35591f 0%, #2a4a1f 55%, #1f3917 100%);
  }
  .card--back .brand { right: 90px; bottom: 120px; font-size: 54px; }
</style>
</head>
<body>

<section class="card card--front" aria-label="Business card front">
  <h1 class="name">Marek <span class="name__last">Tolland</span></h1>
  <div class="divider"></div>
  <ul class="contacts">
    <li>
      <svg viewBox="0 0 24 24" aria-hidden="true"><path fill="#7ab33e" d="M6.6 10.8a15 15 0 0 0 6.6 6.6l2.2-2.2a1 1 0 0 1 1-.25 11.4 11.4 0 0 0 3.6.57 1 1 0 0 1 1 1V20a1 1 0 0 1-1 1A17 17 0 0 1 3 4a1 1 0 0 1 1-1h3.5a1 1 0 0 1 1 1c0 1.25.2 2.45.57 3.57a1 1 0 0 1-.25 1z"/></svg>
      +41 70000 4821
    </li>
    <li>
      <svg viewBox="0 0 24 24" aria-hidden="true"><rect x="2" y="5" width="20" height="14" rx="1.5" fill="#7ab33e"/><path d="M2.5 6l9.5 7 9.5-7" fill="none" stroke="#2b4a20" stroke-width="1.6"/></svg>
      marek@zub.capital
    </li>
    <li>
      <svg viewBox="0 0 24 24" aria-hidden="true"><circle cx="12" cy="12" r="9.5" fill="#7ab33e"/><path d="M2.5 12h19M12 2.5c3 3 3 16 0 19M12 2.5c-3 3-3 16 0 19" fill="none" stroke="#2b4a20" stroke-width="1.4"/></svg>
      www.zub.capital
    </li>
  </ul>
  <p class="location">Geneva, Switzerland</p>
  <p class="brand">Zub Capital</p>
</section>

<section class="card card--back" aria-label="Business card back">
  <div class="pattern" role="img" aria-label="Repeating embossed brand pattern in deep green tones"></div>
  <p class="brand">Zub Capital</p>
</section>

</body>
</html>
```